Fizz's Shed & Grill Burger Restaurant Website - HomePage Only PSD

I need a website design for a restaurant called "Fizz's Shed and Grill" featuring burgers, wings, beer, live music, trivia, and more. I have several images of the restaurant and they already have their logo files created (see attached). I want some type of wood background and integrate the silver tin. This needs to be a modern, hip and fun type design. Design must incorporate these attached graphics.

UPDATE - just added a few more images of things I really like to be incorporated into my designs.
Updates

Industry/Entity Type

Burger Restaurant

Number of Pages Required

1 page

Font styles to use
Sans Serif

Requirements
Must have
• Restaurant/Bar theme with integration of existing logo and the red wood look.
Nice to have
• - Modern Fun appearance
• - Use Pelko Fonts

```html
<!DOCTYPE html>
<html lang="en">
<head>
<meta charset="utf-8">
<title>Fizz's Shed &amp; Grill</title>
<link href="https://fonts.googleapis.com/css2?family=Lobster+Two:wght@400;700&family=Open+Sans:wght@400;600&display=swap" rel="stylesheet">
<style>
:root{
  --wood-dark:#241410;
  --wood-mid:#2f1b15;
  --wood-line:#1a0d0a;
  --panel:#22120e;
  --cream:#f4ead8;
  --text:#e6dccf;
  --muted:#cbbfb1;
  --silver-light:#f2f2f2;
  --silver-dark:#9a9a9a;
  --scroll:#e7c79a;
  --scroll-dark:#b88a55;
  --ink:#2a1a12;
  --wine:#9b1d22;
}
*{box-sizing:border-box;margin:0;padding:0}
html,body{width:1200px;height:2479px;overflow:hidden}
body{
  position:relative;
  background:
    repeating-linear-gradient(90deg,var(--wood-line) 0 2px,transparent 2px 26px,rgba(0,0,0,.25) 26px 28px,transparent 28px 47px),
    linear-gradient(180deg,var(--wood-mid),var(--wood-dark));
  font-family:"Open Sans",Arial,sans-serif;
  color:var(--text);
}
a{text-decoration:none}
.abs{position:absolute}

/* header */
.nav-rule{position:absolute;left:98px;width:1003px;height:3px;background:#4a3229;box-shadow:0 1px 0 #120806}
.nav a{position:absolute;top:60px;font-family:"Lobster Two",Georgia,cursive;font-size:16px;color:#fff;transform:translateX(-50%);white-space:nowrap}
.brand{position:absolute;left:540px;top:10px;width:120px;height:120px;background:var(--wood-dark);display:flex;align-items:center;justify-content:center;text-align:center}
.brand-name{font-family:"Lobster Two",Georgia,cursive;font-size:19px;line-height:23px;color:var(--cream)}

/* slider */
.slider{left:98px;top:139px;width:1003px;height:453px;background:linear-gradient(180deg,var(--silver-light),#b9b9b9);border-radius:6px;padding:10px 11px;box-shadow:0 4px 14px rgba(0,0,0,.6)}
.slide-photo{width:100%;height:433px;border-radius:4px;background:linear-gradient(180deg,#3f6fa8 0%,#6d8fb8 30%,#8a4a2e 45%,#9a5a3a 80%,#6e3a24 100%)}
.arrow{top:362px;width:20px;height:34px}
.down{left:571px;top:563px;width:54px;height:54px;border-radius:50%;background:linear-gradient(180deg,#fafafa,#a8a8a8);box-shadow:0 2px 6px rgba(0,0,0,.6);display:flex;align-items:center;justify-content:center}

/* headings */
.heading{position:absolute;left:0;width:1200px;text-align:center;font-family:"Lobster Two",Georgia,cursive;font-weight:400;font-size:24px;line-height:30px;color:#fff;display:flex;justify-content:center;align-items:center;gap:14px}
.heading svg{width:20px;height:22px}

.intro{left:130px;top:724px;width:940px;text-align:center;font-size:12px;line-height:26.5px;color:var(--text)}
.btn{position:absolute;background:linear-gradient(180deg,#fff,#dcdcdc);border:2px solid #bdbdbd;border-radius:3px;color:var(--ink);font-family:"Lobster Two",Georgia,cursive;display:flex;align-items:center;justify-content:center;box-shadow:0 2px 5px rgba(0,0,0,.6);white-space:nowrap}
.btn-more{left:526px;top:874px;width:145px;height:43px;font-size:16px}

/* features */
.panel{left:99px;top:974px;width:1000px;height:469px;background:rgba(20,9,6,.75);border:1px solid #3e2a22;border-radius:6px;box-shadow:inset 0 0 30px rgba(0,0,0,.7),0 3px 10px rgba(0,0,0,.5)}
.feature{position:absolute;top:1108px;width:190px;transform:translateX(-50%);display:flex;flex-direction:column;align-items:center}
.label{width:174px;height:53px;background:linear-gradient(180deg,var(--scroll),var(--scroll-dark));border-radius:4px;display:flex;align-items:center;justify-content:center;font-family:"Lobster Two",Georgia,cursive;font-size:25px;color:var(--ink)}
.feature-img{width:174px;height:140px;margin-top:21px;border-radius:8px}
.img-burger{background:radial-gradient(ellipse at 50% 50%,#d9a24c 0%,#a9642a 55%,transparent 72%)}
.img-wings{background:radial-gradient(ellipse at 50% 50%,#c0531e 0%,#8a3312 55%,transparent 72%)}
.img-beer{background:radial-gradient(ellipse at 50% 50%,#f1b431 0%,#c47a12 50%,transparent 70%)}
.feature .btn{position:static;width:112px;height:33px;font-size:12px;margin-top:48px}
.note{width:174px;height:140px;margin-top:21px;display:flex;justify-content:center;align-items:center}

/* gallery */
.card{position:absolute;width:322px;height:266px;background:linear-gradient(180deg,#fdfdfd,#a9a9a9);border-radius:3px;padding:10px;box-shadow:0 3px 8px rgba(0,0,0,.6)}
.card-photo{width:100%;height:195px;border-radius:3px}
.card-title{text-align:center;font-family:"Lobster Two",Georgia,cursive;font-size:20px;color:var(--ink);margin-top:18px}
.ph-barn{background:linear-gradient(180deg,#6fa0d8 0%,#a9c4e0 35%,#b34a3a 42%,#d7d0c4 60%,#8a7a5a 100%)}
.ph-sign{background:linear-gradient(180deg,#9aa1a6,#6b5a44 60%,#8f8a7e)}
.ph-steak{background:radial-gradient(ellipse at 50% 75%,#ff8a1e 0%,#a33b10 35%,#1a120e 75%)}
.ph-interior{background:linear-gradient(180deg,#2b3a4a 0%,#8a5a34 30%,#6e4a2c 70%,#2e3f6a 100%)}
.ph-wings{background:radial-gradient(ellipse at 50% 50%,#e08c3a 0%,#a84a1a 40%,#3a0e06 85%)}
.ph-art{background:radial-gradient(ellipse at 50% 45%,#b13a2a 0%,#6e2a1e 35%,#8c8a7a 65%,#9a988a 100%)}

/* footer */
.footer{left:99px;top:2154px;width:1000px;height:235px;background:rgba(20,9,6,.75);border:1px solid #3e2a22;border-radius:6px;box-shadow:inset 0 0 30px rgba(0,0,0,.7)}
.fcol{position:absolute;top:2192px}
.fcol h3{font-family:"Lobster Two",Georgia,cursive;font-weight:400;font-size:16px;color:#fff;text-transform:uppercase;letter-spacing:.5px;margin-bottom:18px}
.fcol p{font-size:12px;line-height:20px;color:var(--muted)}
.about p{width:185px;text-align:justify}
.about .more{margin-top:10px}
.hours p{margin-bottom:12px}
.contact .row{display:flex;gap:16px;align-items:flex-start;margin-bottom:18px}
.contact .row svg{width:14px;height:16px;flex:none;margin-top:3px}
.contact .row p{width:160px}
.social{display:flex;gap:12px}
.social span{width:35px;height:35px;border:2px solid #fff;border-radius:50%}
.search-label{font-family:"Lobster Two",Georgia,cursive;font-size:14px;color:#fff;margin:22px 0 16px}
.search{width:181px;height:30px;background:#fff;display:flex;justify-content:flex-end;align-items:center;padding-right:12px}
.bottom{left:99px;top:2407px;width:1000px;height:72px;background:rgba(20,9,6,.75);border:1px solid #3e2a22;border-bottom:none;border-radius:6px 6px 0 0}
.copy{left:0;top:2430px;width:1200px;text-align:center;font-size:12px;color:var(--text)}

.deco{position:absolute}
</style>
</head>
<body>

<div class="deco" style="left:0;top:612px;width:99px;height:297px;background:radial-gradient(ellipse at 30% 50%,rgba(222,170,70,.85),rgba(160,110,40,.4) 50%,transparent 70%)" role="img" aria-label="Beer glass being poured, decorative photo"></div>
<div class="deco" style="left:1104px;top:909px;width:96px;height:199px;background:radial-gradient(ellipse at 70% 50%,rgba(214,150,60,.9),rgba(130,70,30,.4) 55%,transparent 72%)" role="img" aria-label="Burger, decorative photo"></div>
<div class="deco" style="left:1136px;top:1818px;width:64px;height:166px;background:radial-gradient(ellipse at 80% 50%,rgba(232,210,160,.7),transparent 70%)" role="img" aria-label="Beer glass, decorative photo"></div>
<div class="deco" style="left:0;top:2199px;width:83px;height:181px;background:radial-gradient(ellipse at 20% 50%,rgba(214,150,60,.9),rgba(130,70,30,.4) 55%,transparent 72%)" role="img" aria-label="Burger, decorative photo"></div>

<header>
  <div class="nav-rule" style="top:41px"></div>
  <div class="nav-rule" style="top:95px"></div>
  <nav class="nav">
    <a href="#" style="left:124px">Home</a>
    <a href="#" style="left:240px">About Us</a>
    <a href="#" style="left:363px">Burgers</a>
    <a href="#" style="left:479px">Wings</a>
    <a href="#" style="left:708px">Beer</a>
    <a href="#" style="left:823px">Live music</a>
    <a href="#" style="left:943px">Trivia</a>
    <a href="#" style="left:1066px">Contact Us</a>
  </nav>
  <div class="brand"><span class="brand-name">Fizz's Shed<br>&amp; Grill</span></div>
</header>

<section class="abs slider">
  <div class="slide-photo" role="img" aria-label="Restaurant roof gable with the Fizz's Shed &amp; Grill sign against a blue sky"></div>
</section>
<svg class="abs arrow" style="left:48px" viewBox="0 0 20 34"><path d="M16 5 L5 17 L16 29" fill="none" stroke="#fff" stroke-width="3"/></svg>
<svg class="abs arrow" style="left:1132px" viewBox="0 0 20 34"><path d="M4 5 L15 17 L4 29" fill="none" stroke="#fff" stroke-width="3"/></svg>
<div class="abs down"><svg width="24" height="16" viewBox="0 0 24 16"><path d="M3 3 L12 12 L21 3" fill="none" stroke="#555" stroke-width="3"/></svg></div>

<h2 class="heading" style="top:664px">
  <svg viewBox="0 0 20 22"><path d="M3 9 H17 L15 15 H5 Z M10 15 V21 M6 21 H14" fill="#fff" stroke="#fff" stroke-width="1.5"/></svg>
  Welcome To Fizz's Shed and Grill
  <svg viewBox="0 0 20 22"><path d="M5 2 H15 Q15 11 10 12 Q5 11 5 2 Z" fill="var(--wine)"/><path d="M10 12 V20 M6 20 H14" stroke="#fff" stroke-width="1.5"/></svg>
</h2>
<p class="abs intro">Eu sint homero has. Mel elit aliquando te, mea an nihil quidam senserit. Has an placerat phaedrum. At mutat fuisset sit. Duo no reque nonumes vituperata, ei falli veniam eum, vim te eirmod salutatus interesset. Ex cum dicant scripserit, modo detraxit ne nam, modo aliquando tincidunt ut pri. Eu sint homero has. Mel elit aliquando te, mea an nihil quidam senserit. Has an placerat phaedrum. At mutat fuisset sit. Duo no reque nonumes vituperata, ei falli veniam eum, vim te eirmod salutatus interesset. Ex cum dicant scripserit, modo detraxit ne nam, modo aliquando tincidunt ut pri . At mutat fuisset sit. Duo no reque nonumes vituperata</p>
<a class="btn btn-more" href="#">Read More Info</a>

<section>
  <div class="abs panel"></div>
  <h2 class="heading" style="top:1019px">
    <svg viewBox="0 0 20 22"><path d="M3 9 H17 L15 15 H5 Z M10 15 V21 M6 21 H14" fill="#fff" stroke="#fff" stroke-width="1.5"/></svg>
    Our Restaurant Is About
    <svg viewBox="0 0 20 22"><path d="M5 2 H15 Q15 11 10 12 Q5 11 5 2 Z" fill="var(--wine)"/><path d="M10 12 V20 M6 20 H14" stroke="#fff" stroke-width="1.5"/></svg>
  </h2>
  <div class="feature" style="left:233px">
    <div class="label">Burgers</div>
    <div class="feature-img img-burger" role="img" aria-label="Cheeseburger with lettuce and tomato"></div>
    <a class="btn" href="#">Order Your Dish</a>
  </div>
  <div class="feature" style="left:484px">
    <div class="label">Wings</div>
    <div class="feature-img img-wings" role="img" aria-label="Three glazed chicken wings"></div>
    <a class="btn" href="#">Order Your Dish</a>
  </div>
  <div class="feature" style="left:722px">
    <div class="label">Beer</div>
    <div class="feature-img img-beer" role="img" aria-label="Two glasses of lager beer"></div>
    <a class="btn" href="#">Order Your Dish</a>
  </div>
  <div class="feature" style="left:955px">
    <div class="label">Live Music</div>
    <div class="note"><svg width="80" height="130" viewBox="0 0 80 130"><ellipse cx="26" cy="108" rx="22" ry="17" fill="#fff" transform="rotate(-20 26 108)"/><rect x="42" y="6" width="6" height="100" fill="#fff"/><path d="M48 6 Q52 36 74 50 Q60 40 48 36 Z" fill="#fff"/></svg></div>
    <a class="btn" href="#">Click For Info</a>
  </div>
</section>

<section>
  <h2 class="heading" style="top:1489px">
    <svg viewBox="0 0 20 22"><path d="M3 9 H17 L15 15 H5 Z M10 15 V21 M6 21 H14" fill="#fff" stroke="#fff" stroke-width="1.5"/></svg>
    Our Photo Gallery
    <svg viewBox="0 0 20 22"><path d="M5 2 H15 Q15 11 10 12 Q5 11 5 2 Z" fill="var(--wine)"/><path d="M10 12 V20 M6 20 H14" stroke="#fff" stroke-width="1.5"/></svg>
  </h2>
  <figure class="card" style="left:98px;top:1562px"><div class="card-photo ph-barn" role="img" aria-label="Restaurant exterior with red roof and patio"></div><figcaption class="card-title">Eu Sint Homero Has</figcaption></figure>
  <figure class="card" style="left:440px;top:1562px"><div class="card-photo ph-sign" role="img" aria-label="Tin sign on a wooden entrance wall"></div><figcaption class="card-title">Mel Elit Aliquando Te</figcaption></figure>
  <figure class="card" style="left:779px;top:1562px"><div class="card-photo ph-steak" role="img" aria-label="Steak sizzling over grill flames"></div><figcaption class="card-title">No Eos Ornatus</figcaption></figure>
  <figure class="card" style="left:98px;top:1846px"><div class="card-photo ph-interior" role="img" aria-label="Dining room with wooden wall sign and blue seating"></div><figcaption class="card-title">Eu Sint Homero Has</figcaption></figure>
  <figure class="card" style="left:440px;top:1846px"><div class="card-photo ph-wings" role="img" aria-label="Chicken wings on a hot grill"></div><figcaption class="card-title">No Eos Ornatus</figcaption></figure>
  <figure class="card" style="left:779px;top:1846px"><div class="card-photo ph-art" role="img" aria-label="Painted canvas artwork hanging on a wall"></div><figcaption class="card-title">Mel Elit Aliquando Te</figcaption></figure>
</section>

<footer>
  <div class="abs footer"></div>
  <div class="fcol about" style="left:132px">
    <h3>About</h3>
    <p>Duo ne vero debitis admodum, ea dictas oporteat nam. Nec ad fugit graece facilis, vix ea malorum nominati rationibus, nam equidem sententiae ei.</p>
    <p class="more">[ Read More ]</p>
  </div>
  <div class="fcol hours" style="left:380px">
    <h3>Opening Hours</h3>
    <p>Monday To Friday - 9 AM to 10PM</p>
    <p>Satuday - 10 AM to 10PM</p>
    <p>Sunday - 10 AM to 1PM</p>
  </div>
  <div class="fcol contact" style="left:618px">
    <h3>Contact Us</h3>
    <div class="row"><svg viewBox="0 0 14 16"><path d="M1 8 L7 2 L13 8 M3 7 V15 H11 V7" fill="#fff"/></svg><p>2280 W. Birchline Rd. | Maple Hollow KS 60412</p></div>
    <div class="row"><svg viewBox="0 0 14 16"><rect x="3" y="1" width="8" height="14" rx="1.5" fill="none" stroke="#fff" stroke-width="1.6"/><rect x="6" y="12" width="2" height="1.5" fill="#fff"/></svg><p>Call Us : (555)014-2297</p></div>
    <div class="row"><svg viewBox="0 0 14 16"><rect x="1" y="3" width="12" height="10" fill="none" stroke="#fff" stroke-width="1.5"/><path d="M1 3 L7 9 L13 3" fill="none" stroke="#fff" stroke-width="1.5"/></svg><p>hello@fizzsshed.example</p></div>
  </div>
  <div class="fcol" style="left:860px">
    <h3>Connect Us With</h3>
    <div class="social" aria-label="Social links"><span></span><span></span><span></span><span></span></div>
    <p class="search-label">Search</p>
    <div class="search"><svg width="14" height="14" viewBox="0 0 14 14"><circle cx="6" cy="6" r="4.2" fill="none" stroke="#111" stroke-width="2"/><path d="M9 9 L13 13" stroke="#111" stroke-width="2.2"/></svg></div>
  </div>
  <div class="abs bottom"></div>
  <p class="abs copy">&copy;&nbsp; Companyname 2016 . All Rights Reserved</p>
</footer>

</body>
</html>
```